Dovecote Realty

Business cards for 4 people

They need to say for all
87 Tarrow Quay, Boston MA 02114

Each person will have their own personal information
We would like gold embossing for the name of the company
Marla is the blonde sitting in the chair smiling her information should be on the back of the card with her name and information
Should say for slogan classic pattern, elevated experience
grace@dovecoteprops.com
(413) 555-0182

Odette is the brunette with wavy hair in the tan suit celina@dovecoteprops.com
(617) 555-0137

faith@dovecoteprops.com
(413) 555-0164
standing next to the chair

nora@dovecoteprops.com
(413) 555-0199
close up headshot

```html
<!DOCTYPE html>
<html lang="en">
<head>
<meta charset="utf-8">
<title>Dovecote Realty — Business Card</title>
<link rel="stylesheet" href="https://fonts.googleapis.com/css2?family=Montserrat:wght@400;500;700&display=swap">
<style>
  :root {
    --page: #e9e9e9;
    --navy-deep: #1e2b4a;
    --navy-light: #33445f;
    --navy-text: #1f2d4d;
    --gold: #e0a94e;
    --grey-text: #7a7a7a;
    --card-white: #f4f4f4;
    --card-shade: #e3e3e3;
    --photo-hair: #3a2c28;
    --photo-bg: #c9c6c4;
  }
  * { box-sizing: border-box; margin: 0; padding: 0; }
  html, body { width: 1200px; height: 1200px; overflow: hidden; }
  body {
    background: var(--page);
    font-family: "Montserrat", sans-serif;
    position: relative;
  }
  .card {
    position: absolute;
    left: 233px;
    width: 732px;
    height: 418px;
    box-shadow: 0 6px 18px rgba(0,0,0,0.18);
  }
  .card-front {
    top: 160px;
    background: linear-gradient(135deg, var(--navy-deep) 0%, #24324f 55%, var(--navy-light) 100%);
  }
  .brand-ring {
    position: absolute;
    left: 302px;
    top: 107px;
    width: 128px;
    height: 128px;
    border: 3px solid var(--gold);
    border-radius: 50%;
  }
  .brand-name, .brand-sub {
    position: absolute;
    left: 0;
    right: 0;
    text-align: center;
    color: var(--gold);
    font-weight: 500;
    line-height: 1;
    text-transform: uppercase;
  }
  .brand-name {
    top: 239px;
    font-size: 48px;
    letter-spacing: 1px;
  }
  .brand-sub {
    top: 290px;
    font-size: 22px;
    letter-spacing: 16px;
    padding-left: 16px;
  }
  .card-back {
    top: 632px;
    background: linear-gradient(120deg, var(--card-shade) 0%, var(--card-white) 100%);
  }
  .portrait {
    position: absolute;
    left: 123px;
    top: 129px;
    width: 128px;
    height: 128px;
    border-radius: 50%;
    border: 2px solid var(--gold);
    background: radial-gradient(circle at 55% 45%, #b89c8e 0%, var(--photo-hair) 55%, var(--photo-bg) 100%);
  }
  .rule {
    position: absolute;
    left: 189px;
    top: 255px;
    width: 418px;
    height: 2px;
    background: var(--gold);
  }
  .person-name {
    position: absolute;
    left: 271px;
    top: 132px;
    color: var(--gold);
    font-weight: 700;
    font-size: 31px;
    line-height: 1;
  }
  .person-title {
    position: absolute;
    left: 270px;
    top: 169px;
    color: var(--grey-text);
    font-size: 17px;
    line-height: 20px;
  }
  .contact-line {
    position: absolute;
    left: 270px;
    display: flex;
    align-items: center;
    gap: 8px;
    color: var(--grey-text);
    font-size: 19px;
    height: 24px;
    line-height: 24px;
  }
  .contact-line svg { width: 17px; height: 17px; flex: none; }
  .phone { top: 196px; }
  .mail { top: 224px; }
  .address { top: 263px; }
  .email { letter-spacing: 2.2px; }
  .email .domain { color: var(--navy-text); }
</style>
</head>
<body>
  <section class="card card-front">
    <div class="brand-ring"></div>
    <div class="brand-name">Dovecote</div>
    <div class="brand-sub">Realty</div>
  </section>

  <section class="card card-back">
    <div class="portrait" role="img" aria-label="Headshot of Nora Marston"></div>
    <div class="rule"></div>
    <div class="person-name">Nora Marston</div>
    <div class="person-title">Co-creative Director</div>
    <div class="contact-line phone">
      <svg viewBox="0 0 24 24" aria-hidden="true"><path fill="#e0a94e" d="M6.6 10.8a15 15 0 0 0 6.6 6.6l2.2-2.2a1 1 0 0 1 1-.25 11.4 11.4 0 0 0 3.6.57 1 1 0 0 1 1 1V20a1 1 0 0 1-1 1A17 17 0 0 1 3 4a1 1 0 0 1 1-1h3.5a1 1 0 0 1 1 1c0 1.25.2 2.45.57 3.6a1 1 0 0 1-.25 1z"/></svg>
      <span>(413) 555-0199</span>
    </div>
    <div class="contact-line mail">
      <svg viewBox="0 0 24 24" aria-hidden="true"><path fill="#e0a94e" d="M2 5h20v14H2z"/><path fill="none" stroke="#f1f1f1" stroke-width="1.6" d="M2 5l10 8 10-8"/></svg>
      <span class="email">nora@<span class="domain">dovecoteprops.com</span></span>
    </div>
    <div class="contact-line address">
      <svg viewBox="0 0 24 24" aria-hidden="true"><path fill="#e0a94e" d="M12 2a7 7 0 0 0-7 7c0 5 7 13 7 13s7-8 7-13a7 7 0 0 0-7-7zm0 9.5A2.5 2.5 0 1 1 12 6.5a2.5 2.5 0 0 1 0 5z"/></svg>
      <span>87 Tarrow Quay, Boston MA 02114</span>
    </div>
  </section>
</body>
</html>
```